Bold Flyer Needed for Bold Little Gym

We need a 1 page flyer created for our small boutique fitness facility, CorVanto, which highlights a new service we are offering.
We are now offering Red Light Therapy (RLT) to our members and I need a full color, 1 page flyer created that captures the eye of our members while highlighting the benefits and clearly stating the prices at the bottom of the page.
Flyer will be printed out on a standard 8.5" x 11" sheet of paper and should be laid out in a way that is easy to read. Landscape or Portrait layouts are both expectable.
We are using Silverline Glow Therapy Lights LumaCore 700 Lamps as found here http://lnk.example/7QWRT5Z
I have attached the text that should be included and our logo for branding of the flyer.
Thank you!

```html
<!DOCTYPE html>
<html lang="en">
<head>
<meta charset="utf-8">
<title>CorVanto – Red Light Therapy Room</title>
<link rel="stylesheet" href="https://fonts.googleapis.com/css2?family=Oswald:wght@500;600;700&family=Poppins:wght@400;600;700;800&display=swap">
<style>
  :root {
    --ink: #1c1b1c;
    --yellow: #f5cd16;
    --white: #ffffff;
    --muted: #cfcfcf;
    --backdrop: #e6e4e1;
    --photo-dark: #3a1f24;
    --photo-mid: #7a3340;
    --photo-glow: #e77fb4;
  }
  * { box-sizing: border-box; margin: 0; padding: 0; }
  html, body { width: 1200px; height: 1200px; overflow: hidden; }
  body {
    background: var(--backdrop);
    font-family: "Poppins", sans-serif;
    display: flex; align-items: center; justify-content: center;
  }
  .flyer {
    position: relative; width: 896px; height: 1160px;
    background: var(--ink); overflow: hidden; color: var(--white);
    box-shadow: 0 10px 30px rgba(0,0,0,.25);
  }
  .hero-photo {
    position: absolute; left: 300px; top: 0; width: 596px; height: 640px;
    background:
      linear-gradient(90deg, var(--ink) 0%, rgba(28,27,28,0) 30%),
      linear-gradient(0deg, var(--ink) 0%, rgba(28,27,28,0) 35%),
      radial-gradient(ellipse at 85% 25%, var(--photo-glow) 0%, var(--photo-mid) 35%, var(--photo-dark) 75%);
  }
  .brand {
    position: absolute; left: 40px; top: 40px;
    font-family: "Oswald", sans-serif; font-weight: 700; font-size: 48px;
    color: var(--yellow); line-height: 1;
  }
  .headline {
    position: absolute; left: 40px; top: 130px;
    font-family: "Oswald", sans-serif; font-weight: 700; text-transform: uppercase; line-height: .92;
  }
  .headline .intro { font-size: 44px; font-weight: 600; color: var(--white); }
  .headline .main { font-size: 116px; color: var(--yellow); margin-top: 6px; }
  .headline .room { font-size: 86px; color: var(--white); margin-top: 4px; }
  .headline .rule { width: 250px; height: 4px; background: var(--yellow); margin-top: 12px; }

  .coupon {
    position: absolute; left: 530px; top: 300px; width: 340px;
    background: var(--white); border: 10px solid var(--yellow); border-radius: 6px;
    color: var(--ink); text-align: center; padding: 16px 16px 14px;
  }
  .coupon .limited {
    display: inline-block; border: 3px solid var(--ink); padding: 0 12px;
    font-family: "Oswald", sans-serif; font-weight: 700; font-size: 28px; line-height: 1.3; text-transform: uppercase;
  }
  .coupon .special { font-size: 16px; line-height: 1.4; margin-top: 6px; }
  .coupon .try { font-weight: 800; font-size: 16px; text-transform: uppercase; margin-top: 6px; line-height: 1.2; }
  .coupon .price {
    display: inline-block; background: var(--yellow); border-radius: 14px; padding: 0 26px;
    font-family: "Oswald", sans-serif; font-weight: 700; font-size: 70px; line-height: 1.15; margin-top: 6px;
  }
  .coupon .regular { font-weight: 800; font-size: 19px; line-height: 1.3; text-transform: uppercase; margin-top: 6px; }

  .rlt-intro { position: absolute; left: 40px; top: 550px; width: 420px; }
  .rlt-intro h3 { font-weight: 700; font-size: 14px; line-height: 1.4; margin-bottom: 4px; }
  .rlt-intro p { font-size: 11.5px; line-height: 1.45; color: var(--muted); }

  .benefits { position: absolute; left: 40px; top: 690px; width: 430px; }
  .benefits h2 { font-weight: 800; font-size: 20px; line-height: 1.3; color: var(--yellow); text-transform: uppercase; margin-bottom: 8px; }
  .benefit { margin-bottom: 5px; line-height: 1.3; }
  .benefit strong { display: block; font-size: 13px; color: var(--yellow); font-weight: 700; }
  .benefit span { display: block; font-size: 11px; color: var(--muted); }

  .why {
    position: absolute; left: 480px; top: 645px; width: 416px;
    background: var(--yellow); color: var(--ink); padding: 14px 24px 12px;
  }
  .why h2 { font-weight: 800; font-size: 19px; line-height: 1.3; text-transform: uppercase; margin-bottom: 6px; }
  .why p { font-size: 11px; line-height: 1.35; margin-bottom: 3px; }

  .prices {
    position: absolute; left: 500px; top: 855px; width: 376px;
    border-collapse: collapse; font-size: 12.5px; line-height: 1.4;
  }
  .prices th, .prices td { padding: 4px 10px; text-align: center; border: 2px solid var(--white); white-space: nowrap; }
  .prices .label { background: var(--ink); color: var(--white); text-align: left; font-weight: 600; text-transform: uppercase; }
  .prices .col, .prices .rate { background: var(--yellow); color: var(--ink); font-weight: 700; }

  .call { position: absolute; left: 576px; top: 1008px; width: 300px; text-align: right; }
  .call .lead { display: flex; align-items: center; justify-content: flex-end; gap: 10px; font-size: 18px; font-weight: 600; line-height: 1.3; }
  .call .phone { font-size: 24px; font-weight: 700; line-height: 1.15; }
  .call .note { font-size: 11px; line-height: 1.3; color: var(--muted); }

  .signoff { position: absolute; left: 40px; top: 960px; font-family: "Oswald", sans-serif; text-transform: uppercase; line-height: 1; }
  .signoff .name { font-weight: 700; font-size: 34px; color: var(--white); text-transform: none; }
  .signoff .facility { font-weight: 700; font-size: 40px; color: var(--yellow); margin-top: 4px; }
  .signoff .tagline { font-weight: 500; font-size: 18px; color: var(--white); margin-top: 4px; }

  .contact-band {
    position: absolute; left: 0; bottom: 0; width: 896px; height: 66px; background: var(--yellow);
    color: var(--ink); display: flex; align-items: center; gap: 60px; padding: 0 40px;
  }
  .contact-item { display: flex; align-items: center; gap: 12px; font-size: 14px; font-weight: 600; line-height: 1.3; }
</style>
</head>
<body>
<main class="flyer">
  <div class="hero-photo" role="img" aria-label="Man relaxing beside a glowing red light therapy panel"></div>

  <div class="brand">CorVanto</div>

  <header class="headline">
    <div class="intro">Introducing our new</div>
    <div class="main">Red Light<br>Therapy</div>
    <div class="room">Room!</div>
    <div class="rule"></div>
  </header>

  <section class="coupon">
    <div class="limited">Limited Time Only!</div>
    <div class="special">Special Introductory Offer!</div>
    <div class="try">Try your first session<br>for just</div>
    <div class="price">$25</div>
    <div class="regular">Regularly $55</div>
  </section>

  <section class="rlt-intro">
    <h3>What is Red Light Therapy?</h3>
    <p>Red Light Therapy (RLT) is a revolutionary treatment that uses specific wavelengths of light to promote healing, reduce inflammation, and enhance overall well-being. At CorVanto, we are excited to offer the advanced Silverline Glow Therapy LumaCore 700 panels—designed to maximize your health benefits in a relaxing environment.</p>
  </section>

  <section class="benefits">
    <h2>Benefits of Red Light Therapy:</h2>
    <div class="benefit"><strong>Boosts Energy Levels:</strong><span>Feel revitalized and more energetic after each session.</span></div>
    <div class="benefit"><strong>Enhances Muscle Recovery:</strong><span>Speed up recovery times post workout and reduce soreness.</span></div>
    <div class="benefit"><strong>Improves Skin Health:</strong><span>Reduce wrinkles, blemishes, and promote a youthful glow.</span></div>
    <div class="benefit"><strong>Supports Joint Health:</strong><span>Alleviate pain and inflammation, making movement easier.</span></div>
    <div class="benefit"><strong>Promotes Better Sleep:</strong><span>Improve your sleep patterns and overall restfulness.</span></div>
    <div class="benefit"><strong>Increases Circulation:</strong><span>Enhance blood flow for better nutrient delivery to muscles.</span></div>
  </section>

  <section class="why">
    <h2>Why choose CorVanto?</h2>
    <p>(1) State-of-the-Art Equipment: Experience the power of eight Silverline Glow Therapy LumaCore 700 panels—some of the best on the market!</p>
    <p>(2) Expert Guidance: Our trained staff will guide you through each session to ensure you get the most out of your therapy.</p>
    <p>(3) Community Focused: Join a supportive community that prioritizes health and wellness.</p>
  </section>

  <table class="prices">
    <tr><th class="label">Prices</th><th class="col">CorVanto Member</th><th class="col">Non-Member</th></tr>
    <tr><td class="label">Single Session</td><td class="rate">$35</td><td class="rate">$55</td></tr>
    <tr><td class="label">3 – Pack</td><td class="rate">$102</td><td class="rate">$159</td></tr>
    <tr><td class="label">5 – Pack</td><td class="rate">$167</td><td class="rate">$259</td></tr>
    <tr><td class="label">10 – Pack</td><td class="rate">$316</td><td class="rate">$491</td></tr>
  </table>

  <div class="call">
    <div class="lead">
      <svg width="30" height="30" viewBox="0 0 46 46" aria-hidden="true">
        <circle cx="23" cy="23" r="23" fill="var(--yellow)"/>
        <path d="M15 13c1-1 3-1 4 0l2 3c1 1 0 2-1 3l-1 1c1 3 3 5 6 6l1-1c1-1 2-2 3-1l3 2c1 1 1 3 0 4l-2 2c-7 0-16-9-16-16z" fill="var(--ink)"/>
      </svg>
      <span>Call Us at</span>
    </div>
    <div class="phone">(555) 214- 3080</div>
    <div class="note">to schedule your appointment.</div>
  </div>

  <div class="signoff">
    <div class="name">CorVanto</div>
    <div class="facility">Fitness Facility</div>
    <div class="tagline">Your wellness, our commitment!</div>
  </div>

  <footer class="contact-band">
    <div class="contact-item">
      <svg width="32" height="32" viewBox="0 0 32 32" aria-hidden="true">
        <circle cx="16" cy="16" r="16" fill="var(--ink)"/>
        <path d="M16 8a5 5 0 0 0-5 5c0 4 5 10 5 10s5-6 5-10a5 5 0 0 0-5-5z" fill="var(--white)"/>
        <circle cx="16" cy="13" r="2" fill="var(--ink)"/>
      </svg>
      <span>Street Address Here<br>lorem, 0000</span>
    </div>
    <div class="contact-item">
      <svg width="32" height="32" viewBox="0 0 32 32" aria-hidden="true">
        <circle cx="16" cy="16" r="16" fill="var(--ink)"/>
        <circle cx="16" cy="16" r="8" fill="none" stroke="var(--white)" stroke-width="1.6"/>
        <path d="M8 16h16M16 8c-4 5-4 11 0 16M16 8c4 5 4 11 0 16" fill="none" stroke="var(--white)" stroke-width="1.4"/>
      </svg>
      <span>corvanto.example<br>corvanto.example</span>
    </div>
  </footer>
</main>
</body>
</html>
```